Redesign of LumoWordfind.com in Bootstrap 4

Current design of LumoWordfind.com is not responsive. We need to change it to latest version of Bootstrap 4 keeping essential elements in place.

Apart from home page, we need designs for http://www.lumowordfind.com/meaning/cat also.

Coding

Number of Pages Required

2 page

Colors
34a7d8

Requirements
Must have
• Bootstrap 4

```html
<!DOCTYPE html>
<html lang="en">
<head>
<meta charset="utf-8">
<title>Lumo Wordfind – English Dictionary</title>
<link rel="stylesheet" href="https://fonts.googleapis.com/css2?family=Open+Sans:wght@400;600&family=Lato:wght@400;700&display=swap">
<style>
:root{
  --blue:#34a7d8;
  --orange:#f7941d;
  --dark:#1b1b1b;
  --ink:#222;
  --muted:#555;
  --panel:#f0f0f0;
  --line:#3a3a3a;
}
*{box-sizing:border-box;margin:0;padding:0}
html,body{width:715px;height:1200px;overflow:hidden;background:#fff}
body{position:relative;font-family:"Open Sans",Arial,sans-serif;color:var(--ink)}
.abs{position:absolute}

/* top bar */
.topbar{left:0;top:0;width:715px;height:24px;background:var(--dark)}
.topbar-login{left:345px;top:0;width:370px;height:24px;background:var(--blue);clip-path:polygon(0 0,100% 0,100% 100%,14px 100%)}
.btn-join{left:59px;top:4px;width:78px;height:16px;background:var(--blue);color:#fff;font-size:6.5px;display:flex;align-items:center;justify-content:center;text-transform:uppercase}
.field{background:#fff;font-size:6px;color:#3a5b8a;padding-left:7px;display:flex;align-items:center;height:16px;top:4px}
.btn-login{left:604px;top:4px;width:52px;height:16px;background:var(--orange);color:#fff;font-size:6.5px;display:flex;align-items:center;justify-content:center}

/* header */
.brand{left:57px;top:34px;font-weight:600;font-size:15px;color:#1a1a1a;display:flex;align-items:center;gap:5px}
.brand-mark{width:10px;height:10px;background:var(--orange)}
.nav{left:385px;top:47px;display:flex;gap:18px;font-size:7px;color:#333}
.nav .active{color:var(--orange)}

/* hero */
.hero{left:0;top:80px;width:715px;height:250px;background:radial-gradient(ellipse at 50% 40%,#8a6a3e 0%,#4b3a24 45%,#241a10 100%)}
.search-card{left:58px;top:165px;width:342px;height:89px;background:rgba(30,30,30,.82)}
.search-card h1{position:absolute;left:0;right:0;top:11px;text-align:center;color:#fff;font-weight:400;font-size:12.5px}
.search-input{left:16px;top:47px;width:312px;height:24px;background:#3a3a3a;color:#aaa;font-size:8px;padding-left:10px;display:flex;align-items:center}
.search-btn{left:260px;top:50px;width:64px;height:21px;background:var(--orange);color:#222;font-size:8.5px;display:flex;align-items:center;justify-content:center}
.wotd{left:416px;top:165px;width:241px;height:89px;background:var(--blue)}
.wotd h2{position:absolute;left:0;right:0;top:11px;text-align:center;color:#fff;font-weight:400;font-size:12.5px}
.wotd-box{left:18px;top:31px;width:160px;height:42px;background:#fff}
.wotd-word{left:26px;top:4px;font-size:11.5px;color:#222}
.wotd-phon{left:46px;top:26px;font-size:6.5px;font-style:italic;color:#444}
.wotd-show{left:178px;top:31px;width:43px;height:42px;background:var(--orange);color:#222;font-size:6.5px;text-align:center;display:flex;align-items:center;justify-content:center;line-height:1.4}
.wotd-share{left:18px;top:76px;font-size:5px;color:#123}
.dots{left:348px;top:314px;display:flex;gap:5px}
.dots i{width:4px;height:4px;border-radius:50%;background:#777;display:block}
.dots i.on{background:var(--orange)}

/* features */
.features-title{left:58px;top:368px;font-size:14.5px;font-weight:400}
.features{left:58px;top:400px;list-style:none;font-size:7.5px;line-height:19px}
.features li{display:flex;align-items:center}
.features svg{width:14px;height:6px;margin-right:8px}
.features .free{color:var(--orange);margin-left:3px}
.img-dict{left:343px;top:395px;width:100px;height:65px;background:linear-gradient(160deg,#f4f4f4,#cfd3d8);border-radius:3px}
.ad-top{left:504px;top:362px;width:152px;height:128px;background:linear-gradient(135deg,#f7fbfd,#dbe8ee);border:1px dashed #9cc}
.divider{left:58px;top:510px;width:424px;border-top:1px dotted #bbb}

/* blocks */
.block h3{position:absolute;font-weight:400;font-size:14px}
.thumb{position:absolute;width:91px;height:73px}
.blk-title{font-size:7.5px;font-weight:600}
.blk-text{font-size:6px;line-height:1.45;color:#222;width:100px}
.btn-dark{background:#111;color:#fff;font-size:6.5px;padding:4px 7px;display:inline-block}

/* sidebar */
.sidebar{left:506px;top:511px;width:151px;height:376px;background:var(--panel);border:1px solid #e2e2e2}
.tile{position:absolute;width:63px;height:63px}
.advertise{left:0;right:0;top:364px;text-align:center;font-size:7.5px;color:#3a6ea5}

.ad-banner{left:58px;top:841px;width:372px;height:46px;background:linear-gradient(90deg,#f4ec9c,#efe07a);border:1px solid #888}

/* browse */
.browse{left:0;top:910px;width:715px;height:33px;background:#eef6fb}
.browse-row{left:174px;top:922px;display:flex;font-size:4.8px;color:#445}
.browse-row span{border:1px solid #9ab;height:10px;display:flex;align-items:center;justify-content:center;min-width:11px;background:#fff;margin-right:1px}
.browse-row .label{padding:0 3px;background:#f6f6f6}

/* footer */
.footer{left:0;top:943px;width:715px;height:257px;background:var(--dark);font-family:"Lato",Arial,sans-serif}
.fcol{position:absolute;top:50px;width:104px}
.fcol h4{color:#fff;font-size:9px;letter-spacing:.8px;font-weight:700;margin-bottom:9px}
.fcol a{display:block;color:#aaa;font-size:6.8px;text-decoration:none;padding:5px 1px;border-bottom:1px solid var(--line);white-space:nowrap}
.fcol a:last-child{border-bottom:0}
.subscribe{left:518px;top:50px;width:139px}
.subscribe h4{color:#fff;font-size:9px;letter-spacing:.8px;font-weight:700;margin-bottom:8px}
.subscribe p{color:#aaa;font-size:6.5px;line-height:1.6;margin-bottom:6px}
.sub-field{height:18px;background:#3b3b3b;color:#aaa;font-size:6.5px;padding-left:10px;display:flex;align-items:center;margin-bottom:5px;border-radius:2px}
.sub-btn{height:18px;background:var(--blue);color:#fff;font-size:7px;font-weight:700;letter-spacing:.6px;display:flex;align-items:center;justify-content:center;border-radius:2px}
.footer-bottom{left:0;top:214px;width:715px;border-top:1px solid #333}
.copyright{left:58px;top:233px;color:#ddd;font-size:6.5px}
.social{right:50px;top:233px;display:flex;gap:7px;color:#fff;font-size:6px}
.version{left:692px;top:233px;color:#ccc;font-size:6.5px}
</style>
</head>
<body>

<header>
  <div class="abs topbar"></div>
  <div class="abs topbar-login"></div>
  <div class="abs btn-join">Join for free</div>
  <div class="abs field" style="left:364px;width:115px">User Name</div>
  <div class="abs field" style="left:482px;width:115px">Password</div>
  <div class="abs btn-login">LOGIN</div>

  <div class="abs brand"><span class="brand-mark"></span>Lumo Wordfind</div>
  <nav class="abs nav">
    <span class="active">Home</span><span>Idioms</span><span>Common Errors</span><span>Crossword</span><span>Blog</span><span>Contact</span>
  </nav>
</header>

<section class="abs hero" role="img" aria-label="Open book on a wooden table with letters floating above it"></section>
<div class="abs search-card">
  <h1>Lumo English Dictionary</h1>
  <div class="abs search-input">Enter a word or prahse</div>
  <div class="abs search-btn">Search</div>
</div>
<div class="abs wotd">
  <h2>Word of the Day</h2>
  <div class="abs wotd-box">
    <div class="abs wotd-word">exhaustive <span style="font-size:6px;color:#888">◂</span></div>
    <div class="abs wotd-phon">/ɪɡˈzɔːstɪv/</div>
  </div>
  <div class="abs wotd-show">Show<br>Defenition</div>
  <div class="abs wotd-share">Feedline · Chirply</div>
</div>
<div class="abs dots"><i></i><i></i><i class="on"></i></div>

<h2 class="abs features-title">Search, Save and Master Words</h2>
<ul class="abs features">
  <li><svg viewBox="0 0 14 6"><path d="M0 3H12M9 0.5L12 3 9 5.5" stroke="#34a7d8" fill="none"/></svg>Search from more than 300,000 words and phrases</li>
  <li><svg viewBox="0 0 14 6"><path d="M0 3H12M9 0.5L12 3 9 5.5" stroke="#34a7d8" fill="none"/></svg>Multiple usages to clarify the context</li>
  <li><svg viewBox="0 0 14 6"><path d="M0 3H12M9 0.5L12 3 9 5.5" stroke="#34a7d8" fill="none"/></svg>Audio, phonetics, meanings, synonyms and antonyms</li>
  <li><svg viewBox="0 0 14 6"><path d="M0 3H12M9 0.5L12 3 9 5.5" stroke="#34a7d8" fill="none"/></svg>Save the words to your personal deck and access from anywhere</li>
  <li><svg viewBox="0 0 14 6"><path d="M0 3H12M9 0.5L12 3 9 5.5" stroke="#34a7d8" fill="none"/></svg>It's<span class="free">FREE</span></li>
</ul>
<div class="abs img-dict" role="img" aria-label="Open dictionary"></div>
<div class="abs ad-top" role="img" aria-label="Advertisement for shoes at a discounted price"></div>
<div class="abs divider"></div>

<section class="block">
  <h3 style="left:58px;top:534px">English Tidbit</h3>
  <div class="thumb" style="left:58px;top:573px;background:linear-gradient(135deg,#eee,#bbb)" role="img" aria-label="Scattered letters spelling words"></div>
  <div class="abs" style="left:163px;top:573px">
    <div class="blk-title">gaffe/gaff</div>
    <p class="blk-text" style="margin-top:8px">"Gaffe" is a social blunder and "gaff" is a large hook. Be warned not to make the gaffe of mixing it up with gaff.</p>
  </div>

  <h3 style="left:280px;top:534px">Daily Crossword</h3>
  <div class="thumb" style="left:280px;top:573px;background:linear-gradient(135deg,#ddd,#777)" role="img" aria-label="Crossword grid with a pen"></div>
  <div class="abs" style="left:385px;top:573px">
    <div class="blk-title">Crossword Lovers!</div>
    <p class="blk-text" style="margin-top:8px">Take this daily crossword challenge from Lumo Wordfind.</p>
    <span class="btn-dark" style="margin-top:17px">Solve Now</span>
  </div>

  <h3 style="left:58px;top:672px">Emberfox Addon</h3>
  <div class="thumb" style="left:58px;top:710px;background:linear-gradient(180deg,#fafafa,#e6e6ee);border:1px solid #eee" role="img" aria-label="Addon popup showing a word definition"></div>
  <div class="abs" style="left:163px;top:710px">
    <p class="blk-text">Add this tool to your Emberfox and quickly look up for definitions from any website without leaving the page.</p>
    <span class="btn-dark" style="margin-top:21px">Get It Now</span>
  </div>

  <h3 style="left:280px;top:672px">Designed for Orbphone</h3>
  <div class="thumb" style="left:280px;top:710px;background:linear-gradient(180deg,#fff,#e8e8e8);border:1px solid #e5e5e5" role="img" aria-label="Smartphone showing the dictionary app"></div>
  <div class="abs" style="left:385px;top:710px">
    <p class="blk-text">Lumo Wordfind is specially designed for your Orbphone to quickly lookup meaining, usages and audio of words.</p>
  </div>
</section>

<aside class="abs sidebar">
  <div class="tile" style="left:9px;top:8px;background:#e86a7a" role="img" aria-label="Advertisement tile"></div>
  <div class="tile" style="left:79px;top:8px;background:#35b34a" role="img" aria-label="Advertisement tile"></div>
  <div class="tile" style="left:9px;top:79px;background:#2d3540" role="img" aria-label="Advertisement tile"></div>
  <div class="tile" style="left:79px;top:79px;background:#3c4a3a" role="img" aria-label="Advertisement tile"></div>
  <div class="tile" style="left:9px;top:150px;background:linear-gradient(#f3d66a,#9cc24a)" role="img" aria-label="Advertisement tile"></div>
  <div class="tile" style="left:79px;top:150px;background:linear-gradient(#fff,#f4b060)" role="img" aria-label="Advertisement tile"></div>
  <div class="tile" style="left:9px;top:220px;background:linear-gradient(135deg,#ccd,#667)" role="img" aria-label="Advertisement tile"></div>
  <div class="tile" style="left:79px;top:220px;background:linear-gradient(135deg,#eee,#d9b98a)" role="img" aria-label="Advertisement tile"></div>
  <div class="tile" style="left:9px;top:291px;background:#2a2f36" role="img" aria-label="Advertisement tile"></div>
  <div class="abs advertise">Advertise Here</div>
</aside>

<div class="abs ad-banner" role="img" aria-label="Pizza discount advertisement banner"></div>

<div class="abs browse"></div>
<div class="abs browse-row">
  <span class="label">Browse Dictionary</span><span>A</span><span>B</span><span>C</span><span>D</span><span>E</span><span>F</span><span>G</span><span>H</span><span>I</span><span>J</span><span>K</span><span>L</span><span>M</span><span>N</span><span>O</span><span>P</span><span>Q</span><span>R</span><span>S</span><span>T</span><span>U</span><span>V</span><span>W</span><span>X</span><span>Y</span><span>Z</span>
</div>

<footer class="abs footer">
  <div class="fcol" style="left:59px"><h4>MENU 1</h4><a>LumoWordfind.com</a><a>FAQ</a><a>Contact</a><a>Blog</a></div>
  <div class="fcol" style="left:212px"><h4>MENU 2</h4><a>Legal</a><a>Privacy Policy</a><a>Terms of Use</a></div>
  <div class="fcol" style="left:365px"><h4>MENU 3</h4><a>Others</a><a>Popular Words</a><a>Common Errors in English</a><a>Diploma Prep Online</a></div>
  <div class="abs subscribe">
    <h4>SUBSCRIBE TO NEWS</h4>
    <p>Lorem ipsum dolor sit amet, consectetur adipiscing elit.</p>
    <div class="sub-field">Name</div>
    <div class="sub-field">Email</div>
    <div class="sub-btn">SUBSCRIBE</div>
  </div>
  <div class="abs footer-bottom"></div>
  <div class="abs copyright">Copyright 2016 yoursite &nbsp;|&nbsp; All Rights Reserved</div>
  <div class="abs social"><span>Friendlo</span><span>Chirply</span><span>Pinboardly</span><span>Circlo</span></div>
  <div class="abs version">M3</div>
</footer>

</body>
</html>
```